New Coffee Shop business card

We are opening our new coffee shop and are needing business cards to take with us on February 6th to Atlanta, Ga to a show.

We will be offering the following menu type items:

coffee
teas
espresso
frappes
smoothies

sandwiches
soups
salads
pastries
ice cream

Our shop is in a rural country-side area and we would like to convey that feel in our shop. In addition to the cafe we will also be selling gifts and furniture and other home decor. Much of this merchandise will be rescued, refurbished or repurposed which is also a core value of what we are all about.

We have a company logo we would like incorporated into the design.

We will also provide files that have the elements of the logo which may also be useful in the design of the card.

Since we are not open yet we need one slightly altered version of the card as well as the final product which states "Opening in the summer 2015"

Target Market(s)

moderate to slightly upscale and folksy.

Industry/Entity Type

Coffee Shop

Contact Information for Business Card

Fern Kettle Coffee
name
address
phone number
email

Card

Font styles to use
Sans Serif

Requirements
Must have
• Must include Logo
• Must include information on menu.
• Must include information on our merchandise sales as described inthe project description.
• Color scheme to complement the logo
Nice to have
• The following descriptions
• "We are also selling gifts, furniture, and other home decoration."
• "We rescue, refurbish, and repurpose old furniture so it can live again."

```html
<!DOCTYPE html>
<html lang="en">
<head>
<meta charset="utf-8">
<title>Fern Kettle Coffee – Business Card</title>
<link rel="stylesheet" href="https://fonts.googleapis.com/css2?family=Arimo:wght@400;700&family=Questrial&display=swap">
<style>
  :root {
    --page: #e9e5df;
    --charcoal: #2f3033;
    --wine: #7c2a31;
    --wine-bright: #8a2a33;
    --ink: #111111;
    --paper: #ffffff;
    --sand: #c2b8a3;
    --logo-grey: #3a3a3c;
    --ghost: rgba(255,255,255,0.08);
  }
  * { margin: 0; padding: 0; box-sizing: border-box; }
  html, body { width: 1200px; height: 1200px; overflow: hidden; background: var(--page); }
  .canvas { position: relative; width: 1200px; height: 1200px; font-family: "Questrial", sans-serif; }

  .card { position: absolute; left: 122px; width: 962px; overflow: hidden; box-shadow: 0 3px 10px rgba(0,0,0,0.25); }
  .card--front { top: 26px; height: 562px; background: var(--paper); }
  .card--back { top: 610px; height: 564px; background: var(--ink); }
  .card svg.bg { position: absolute; inset: 0; }

  /* front */
  .cup-mark { position: absolute; left: 100px; top: 160px; width: 200px; height: 260px; background: var(--ghost); border-radius: 40px 40px 90px 90px; }
  .contact { position: absolute; left: 30px; top: 120px; width: 340px; color: var(--paper); text-align: center; }
  .contact__name { font-family: "Arimo", sans-serif; font-weight: 700; font-size: 36px; }
  .contact__role { font-size: 26px; margin-top: 4px; }
  .contact__address { font-size: 24px; margin-top: 16px; line-height: 1.35; }
  .contact__line { font-size: 24px; margin-top: 12px; }
  .contact__line + .contact__line { margin-top: 6px; }

  .brand { position: absolute; text-align: center; font-size: 54px; line-height: 1.05; }
  .brand__dot { display: block; width: 70px; height: 70px; border-radius: 50%; margin: 0 auto 22px; }
  .brand--front { left: 560px; top: 140px; width: 380px; color: var(--logo-grey); }
  .brand--front .brand__dot { background: var(--wine); }
  .brand--back { left: 560px; top: 130px; width: 380px; color: var(--paper); }
  .brand--back .brand__dot { background: var(--paper); }

  .merch-band { position: absolute; left: 0; bottom: 0; width: 100%; height: 72px; background: var(--sand); color: var(--ink); text-align: center; font-size: 22px; line-height: 30px; padding-top: 6px; }

  /* back */
  .menu-intro { position: absolute; left: 74px; top: 30px; width: 400px; text-align: center; color: var(--paper); font-size: 29px; line-height: 1.25; }
  .menu-list { position: absolute; list-style: none; color: var(--paper); font-size: 30px; line-height: 39.5px; }
  .menu-list li::before { content: ""; display: inline-block; width: 12px; height: 12px; background: var(--paper); border-radius: 50%; margin-right: 14px; vertical-align: middle; }
  .menu-list--food { left: 52px; top: 128px; }
  .menu-list--drinks { left: 292px; top: 344px; }
</style>
</head>
<body>
<main class="canvas">

  <section class="card card--front">
    <svg class="bg" width="962" height="562" viewBox="0 0 962 562" aria-hidden="true">
      <defs>
        <linearGradient id="panelFade" x1="0" x2="1" y1="0" y2="0">
          <stop offset="0" stop-color="#2f3033"/>
          <stop offset="1" stop-color="#7c2a31"/>
        </linearGradient>
      </defs>
      <path d="M0 0 H555 C470 110 610 220 500 320 C440 380 455 440 470 490 H0 Z" fill="url(#panelFade)"/>
    </svg>
    <div class="cup-mark" role="img" aria-label="Faint steaming coffee cup decoration"></div>
    <div class="contact">
      <p class="contact__name">Your Name Here</p>
      <p class="contact__role">Owner</p>
      <p class="contact__address">Ex-42 Meadow Bend Loop<br>Harlow Creek</p>
      <p class="contact__line">Phone: 555-0148-2297</p>
      <p class="contact__line">Email: email@yourmail.com</p>
    </div>
    <div class="brand brand--front"><span class="brand__dot"></span>Fern Kettle<br>Coffee</div>
    <div class="merch-band">
      <p>We are also selling gifts, furniture, and other home decoration</p>
      <p>We rescue, refurbish, and repurpose old furniture so it can live again</p>
    </div>
  </section>

  <section class="card card--back">
    <svg class="bg" width="962" height="564" viewBox="0 0 962 564" aria-hidden="true">
      <path d="M0 300 C150 380 350 380 560 300 C720 240 850 220 962 230 V564 H0 Z" fill="var(--wine-bright)"/>
    </svg>
    <p class="menu-intro">We will be offering the following menu type items</p>
    <ul class="menu-list menu-list--food">
      <li>sandwiches</li><li>soups</li><li>salads</li><li>pastries</li><li>ice cream</li>
    </ul>
    <ul class="menu-list menu-list--drinks">
      <li>coffee</li><li>teas</li><li>espresso</li><li>frappes</li><li>smoothies</li>
    </ul>
    <div class="brand brand--back"><span class="brand__dot"></span>Fern Kettle<br>Coffee</div>
  </section>

</main>
</body>
</html>
```